Verodex business card

Business card for sustainable investment company called "Verodex". Verodex is an exchange platform selling carbon credits between buyers and sellers. Carbon Credits are an environmental commodity for reducing global carbon emissions.

the card should obviously have our logo and the theme should be sustainability/environment mixed with a trading platform.

Contact Information for Business Card

Logo, Name, Title, Phone, Email

Colors
0054AA
0677BA
7BADD7
CADEEF
E8F1F8
0094D4
00A9DD
6FCCEA
C7EBF8
E9F6FB
00AB8E
00BBA5
67D7C9
C6EFE9
E9F9F6
59FF00
82FF00
B8FF75
E3FFCB
F4FFEA

```html
<!DOCTYPE html>
<html lang="en">
<head>
<meta charset="utf-8">
<title>Verodex business card</title>
<link href="https://fonts.googleapis.com/css2?family=Montserrat:wght@600&family=Arimo:wght@400;700&display=swap" rel="stylesheet">
<style>
  :root {
    --page: #e4e7ec;
    --navy: #1b2c47;
    --navy-deep: #14223a;
    --paper: #f1f2f4;
    --white: #ffffff;
    --accent-blue: #1a6fd8;
    --ink: #1d1f24;
  }
  * { box-sizing: border-box; margin: 0; padding: 0; }
  html, body { width: 1200px; height: 874px; overflow: hidden; }
  body {
    background: var(--page);
    display: flex; flex-direction: column; align-items: center; justify-content: center;
    gap: 40px;
    font-family: "Arimo", Arial, sans-serif;
  }
  .card {
    position: relative;
    width: 640px; height: 366px;
    border-radius: 18px;
    background: var(--navy);
    overflow: hidden;
    box-shadow: 0 10px 26px rgba(20, 30, 50, 0.25);
  }
  .brand {
    display: flex; align-items: center; gap: 18px;
    font-family: "Montserrat", Arial, sans-serif;
    font-weight: 600;
    color: var(--white);
    letter-spacing: 1px;
  }
  .brand-mark { display: block; background: var(--white); }

  .card-front .brand {
    position: absolute; left: 50%; top: 50%;
    transform: translate(-50%, -50%);
    font-size: 56px;
  }
  .card-front .brand-mark { width: 44px; height: 44px; }

  .card-back .backdrop-mark {
    position: absolute; left: 70px; top: 70px;
    width: 170px; height: 170px;
    background: var(--navy-deep);
    border-radius: 6px;
  }
  .card-back .brand-name {
    position: absolute; left: 48px; top: 258px;
    font-family: "Montserrat", Arial, sans-serif;
    font-weight: 600; font-size: 50px;
    color: var(--white); letter-spacing: 1px;
  }
  .card-back .contact-panel { position: absolute; inset: 0; }
  .contact {
    position: absolute; left: 388px; top: 140px;
  }
  .contact-name {
    font-weight: 700; font-size: 26px; color: var(--accent-blue); line-height: 1;
  }
  .contact-title {
    font-weight: 700; font-size: 17px; color: var(--ink); margin-top: 4px;
  }
  .contact-lines { list-style: none; margin-top: 26px; }
  .contact-lines li {
    display: flex; align-items: center; gap: 8px;
    font-size: 17px; color: var(--ink); line-height: 24px;
  }
  .contact-lines svg { width: 14px; height: 14px; flex: none; }
</style>
</head>
<body>
  <section class="card card-front">
    <div class="brand">
      <span class="brand-mark"></span>
      <span class="brand-name">VERODEX</span>
    </div>
  </section>

  <section class="card card-back">
    <span class="backdrop-mark"></span>
    <span class="brand-name">VERODEX</span>
    <svg class="contact-panel" width="640" height="366" viewBox="0 0 640 366">
      <polygon points="470,0 640,0 640,366 390,366 350,180" fill="var(--paper)"/>
    </svg>
    <div class="contact">
      <p class="contact-name">Daniel Marsh</p>
      <p class="contact-title">President</p>
      <ul class="contact-lines">
        <li>
          <svg viewBox="0 0 24 24"><path fill="var(--accent-blue)" d="M6.6 10.8a15.1 15.1 0 0 0 6.6 6.6l2.2-2.2c.3-.3.7-.4 1-.2 1.1.4 2.3.6 3.6.6.6 0 1 .4 1 1V20c0 .6-.4 1-1 1A17 17 0 0 1 3 4c0-.6.4-1 1-1h3.5c.6 0 1 .4 1 1 0 1.3.2 2.5.6 3.6.1.3 0 .7-.2 1z"/></svg>
          (555) 0142-7781
        </li>
        <li>
          <svg viewBox="0 0 24 24"><rect x="2" y="5" width="20" height="14" rx="2" fill="var(--accent-blue)"/><path d="M3 6l9 7 9-7" fill="none" stroke="var(--paper)" stroke-width="1.8"/></svg>
          info@verodex.com
        </li>
      </ul>
    </div>
  </section>
</body>
</html>
```